Business Card for Multi-Brand Sportswear Company

We are looking for a business card which represents our company and the multiple brands within it.

The company: Fen Athletics (LTD)
The brands: Fen, TavaPuni, ElmStretch, Grit and Rain

Employees using these cards would be representing Fen Athletics, rather than any of the individual brands. You will see a current design within the uploaded files, to give some inspiration. The actual text of the brands is not necessary, but the logos should be on there is some format.

Our creative minds on this are stretched, so we are looking for someone to make this their own, and show us what a good business card should look like.

We may like to get these printed with spot gloss, so keep that in mind with your designs.

www.fenathletics.co.uk

Industry/Entity Type

Business

Contact Information for Business Card

Leo Pemberton-Hale
Operations Manager
(+44) 1632 960 418
Leo@fenathletics.co.uk
www.fenathletics.co.uk

Font styles to use
Sans Serif
Other font styles liked:
• Eurostile

Colors
ffffff

Requirements
Nice to have
• Dark (black) background

```html
<!DOCTYPE html>
<html lang="en">
<head>
<meta charset="utf-8">
<title>Fen Athletics – Business Card</title>
<link rel="stylesheet" href="https://fonts.googleapis.com/css2?family=Saira:wght@400;500;600&display=swap">
<style>
  :root {
    --bg: #3a3a3a;
    --paper: #ffffff;
    --ink: #1a1a1a;
    --muted: #444444;
    --red: #ec1c24;
    --band: #0d0d0d;
  }
  * { box-sizing: border-box; margin: 0; padding: 0; }
  html, body {
    width: 1105px; height: 1200px; overflow: hidden;
    background: var(--bg);
    font-family: "Saira", sans-serif;
  }
  .card {
    position: absolute; left: 192px; width: 720px; height: 412px;
    overflow: hidden;
  }
  .card--front { top: 145px; background: var(--paper); }
  .card--back { top: 601px; background: var(--red); }

  .wordmark {
    position: absolute; font-weight: 600; letter-spacing: 1px; white-space: nowrap;
  }
  .card--front .wordmark {
    right: 40px; top: 72px; font-size: 44px; color: var(--ink);
  }
  .card--back .wordmark {
    left: 0; right: 0; text-align: center; top: 138px; font-size: 62px; color: var(--paper);
  }

  .person { position: absolute; left: 41px; top: 222px; }
  .person__name { font-size: 26px; font-weight: 600; color: var(--red); line-height: 1.2; }
  .person__role { font-size: 19px; color: var(--ink); line-height: 1.3; }

  .rule {
    position: absolute; left: 41px; right: 41px; top: 290px; height: 1.5px; background: var(--ink);
  }

  .contacts { position: absolute; left: 41px; top: 300px; list-style: none; }
  .contacts li {
    display: flex; align-items: center; gap: 10px;
    font-size: 19px; color: var(--muted); height: 28px;
  }
  .contacts svg { width: 18px; height: 18px; fill: var(--red); }

  .address {
    position: absolute; right: 41px; top: 300px; text-align: right;
    font-size: 19px; color: var(--muted); line-height: 28px; font-style: normal;
  }

  .web-band {
    position: absolute; left: 0; right: 0; bottom: 0; height: 37px; background: var(--band);
    color: var(--paper); font-size: 18px; line-height: 37px; padding-left: 48px;
  }

  .brands {
    position: absolute; left: 40px; right: 40px; top: 340px;
    display: flex; justify-content: space-between; align-items: center; list-style: none;
  }
  .brands li {
    display: flex; align-items: center; gap: 8px;
    color: var(--paper); font-size: 20px; font-weight: 500;
  }
  .brand__dot { width: 14px; height: 14px; border: 2px solid var(--paper); border-radius: 50%; }
</style>
</head>
<body>
  <section class="card card--front" aria-label="Business card front">
    <div class="wordmark">FEN ATHLETICS</div>

    <div class="person">
      <p class="person__name">Owen Thackray</p>
      <p class="person__role">Managing Director</p>
    </div>

    <div class="rule"></div>

    <ul class="contacts">
      <li>
        <svg viewBox="0 0 24 24" aria-hidden="true"><path d="M6.6 10.8a15.1 15.1 0 0 0 6.6 6.6l2.2-2.2a1 1 0 0 1 1-.25 11.4 11.4 0 0 0 3.6.57 1 1 0 0 1 1 1V20a1 1 0 0 1-1 1A17 17 0 0 1 3 4a1 1 0 0 1 1-1h3.5a1 1 0 0 1 1 1c0 1.25.2 2.45.57 3.57a1 1 0 0 1-.25 1z"/></svg>
        +44 (0)1632 960418
      </li>
      <li>
        <svg viewBox="0 0 24 24" aria-hidden="true"><path d="M2 5h20v2l-10 6L2 7z"/><path d="M2 9l10 6 10-6v10H2z"/></svg>
        owen@fenathletics.co.uk
      </li>
    </ul>

    <address class="address">Marsh Yard, Ellerby<br>Hollin, ZZ1 4QT</address>

    <div class="web-band">www.fenathletics.co.uk</div>
  </section>

  <section class="card card--back" aria-label="Business card back">
    <div class="wordmark">FEN ATHLETICS</div>

    <ul class="brands">
      <li><span class="brand__dot"></span>TavaPuni</li>
      <li>ElmStretch</li>
      <li>Grit and Rain</li>
      <li>Fen</li>
    </ul>
  </section>
</body>
</html>
```